Redesign of Velvet Groove Entertainment Card

I already have my logo and font design for my company name. I am looking to come up with a Unique way of having it on my business card. Just looking for a really hip, and professional business card while still using my logo design.

I have also enclosed the front and back of the card so you can see what I have now. Looking for something different.

Thank you!

Target Market(s)

Young to middle aged brides and grooms

Industry/Entity Type

Business

Requirements
Should not have
• Cheese

```html
<!DOCTYPE html>
<html lang="en">
<head>
<meta charset="utf-8">
<title>Velvet Groove Entertainment – Business Card</title>
<link rel="stylesheet" href="https://fonts.googleapis.com/css2?family=Open+Sans:wght@400;600;800&display=swap">
<style>
  :root {
    --backdrop: #c9c9c9;
    --card: #1d1b1c;
    --card-edge: #2a2829;
    --brand-blue: #2f6fe0;
    --title-blue: #3b55c4;
    --text-light: #f2f2f2;
    --text-soft: #d6d6d6;
    --text-muted: #8e9bb5;
  }
  * { box-sizing: border-box; margin: 0; padding: 0; }
  html, body {
    width: 1200px;
    height: 1155px;
    overflow: hidden;
    background: var(--backdrop);
    font-family: "Open Sans", "Helvetica Neue", Arial, sans-serif;
  }
  .sheet {
    width: 1200px;
    height: 1155px;
    display: flex;
    flex-direction: column;
    align-items: center;
    justify-content: center;
    gap: 60px;
  }
  .card {
    width: 840px;
    height: 480px;
    background: var(--card);
    border: 1px solid var(--card-edge);
    box-shadow: 0 10px 26px rgba(0,0,0,0.25);
    position: relative;
    color: var(--text-light);
  }

  /* Front */
  .card--front {
    display: flex;
    flex-direction: column;
    align-items: center;
    justify-content: center;
    gap: 64px;
  }
  .brand {
    display: flex;
    align-items: center;
    gap: 26px;
  }
  .brand__dot {
    width: 118px;
    height: 118px;
    border-radius: 50%;
    background: var(--brand-blue);
    flex: none;
  }
  .brand__words { display: flex; flex-direction: column; }
  .brand__name {
    font-size: 64px;
    font-weight: 800;
    line-height: 1;
    letter-spacing: 4px;
    text-transform: uppercase;
    color: var(--brand-blue);
  }
  .brand__tagline {
    margin-top: 12px;
    font-size: 15px;
    font-weight: 600;
    letter-spacing: 1.5px;
    text-transform: uppercase;
    color: var(--text-muted);
  }
  .services {
    text-align: center;
    font-size: 27px;
    line-height: 1.5;
    color: var(--text-soft);
  }

  /* Back */
  .card--back {
    display: flex;
    flex-direction: column;
    align-items: center;
    padding-top: 78px;
  }
  .person__name {
    font-size: 32px;
    font-weight: 400;
    color: var(--text-light);
    text-align: center;
  }
  .person__title {
    font-size: 26px;
    color: var(--title-blue);
    text-align: center;
    margin-top: 2px;
  }
  .contacts {
    list-style: none;
    margin-top: 44px;
    display: flex;
    flex-direction: column;
    gap: 10px;
    font-size: 24px;
    color: var(--text-light);
  }
  .contacts li { display: flex; align-items: center; gap: 12px; }
  .contacts svg { width: 24px; height: 24px; flex: none; fill: var(--title-blue); }
  .contact__marker {
    width: 20px; height: 20px; border-radius: 50%;
    background: var(--title-blue); flex: none; margin: 0 2px;
  }
</style>
</head>
<body>
<main class="sheet">

  <section class="card card--front" aria-label="Card front">
    <div class="brand">
      <span class="brand__dot" aria-hidden="true"></span>
      <div class="brand__words">
        <span class="brand__name">Velvet Groove</span>
        <span class="brand__tagline">Entertainment &amp; Event Professionals</span>
      </div>
    </div>
    <p class="services">
      Djs / Emcees | Lighting / Wireless LED Uplighting<br>
      Photo Booths | Photo Montages
    </p>
  </section>

  <section class="card card--back" aria-label="Card back">
    <h1 class="person__name">Marco Bellamy</h1>
    <p class="person__title">Owner / Emcee</p>
    <ul class="contacts">
      <li>
        <svg viewBox="0 0 24 24" aria-hidden="true"><path d="M6.6 10.8c1.4 2.8 3.8 5.1 6.6 6.6l2.2-2.2c.3-.3.7-.4 1-.2 1.1.4 2.3.6 3.6.6.6 0 1 .4 1 1V20c0 .6-.4 1-1 1C10.6 21 3 13.4 3 4c0-.6.4-1 1-1h3.5c.6 0 1 .4 1 1 0 1.3.2 2.5.6 3.6.1.3 0 .7-.2 1l-2.3 2.2z"/></svg>
        <span>555 019 4172</span>
      </li>
      <li>
        <svg viewBox="0 0 24 24" aria-hidden="true"><path d="M2 5h20v14H2z M3.5 6.5 12 13l8.5-6.5" fill="var(--title-blue)" stroke="var(--card)" stroke-width="1.4"/></svg>
        <span>info@velvetgroove.com</span>
      </li>
      <li>
        <svg viewBox="0 0 24 24" aria-hidden="true"><circle cx="12" cy="12" r="10"/><path d="M2 12h20M12 2c3 3 3 17 0 20M12 2c-3 3-3 17 0 20" fill="none" stroke="var(--card)" stroke-width="1.4"/></svg>
        <span>www.velvetgroove.com</span>
      </li>
      <li>
        <span class="contact__marker" aria-hidden="true"></span>
        <span>velvetgrooveentertainment</span>
      </li>
    </ul>
  </section>

</main>
</body>
</html>
```